Veldmark Supplies Business Card

Professional business card that stand out to our potential customers. Front and back with clean modern design

Industry/Entity Type

Oil and gas

Contact Information for Business Card

Name, address, website , office phone and cell number

Requirements
Must have
• Editable files for each employee

```html
<!DOCTYPE html>
<html lang="en">
<head>
<meta charset="UTF-8">
<title>Veldmark Supplies Business Card</title>
<link href="https://fonts.googleapis.com/css2?family=Roboto:wght@400;700&display=swap" rel="stylesheet">
<style>
  :root {
    --stage: #3b3b3d;
    --card-front: #1a1a1b;
    --card-back: #2b2b2c;
    --pattern-light: #232324;
    --pattern-dark: #151516;
    --ink: #e4e4e4;
    --ink-soft: #c9c9c9;
    --rule: #8a8a8a;
    --accent-red: #e8202a;
    --accent-blue: #1fb3d6;
  }
  * { margin: 0; padding: 0; box-sizing: border-box; }
  html, body { width: 1200px; height: 694px; overflow: hidden; }
  body {
    background: var(--stage);
    font-family: "Roboto", Arial, sans-serif;
    color: var(--ink);
    position: relative;
  }
  .card {
    position: absolute;
    top: 197px;
    width: 520px;
    height: 300px;
    border-radius: 28px;
    overflow: hidden;
  }
  .card-front { left: 50px; background: var(--card-front); }
  .card-back { left: 630px; background: var(--card-back); }

  .front-pattern {
    position: absolute; inset: 0;
    background: linear-gradient(135deg, var(--pattern-light), var(--pattern-dark));
  }
  .front-brand {
    position: absolute; left: 0; right: 0; top: 0; bottom: 0;
    display: flex; align-items: center; justify-content: center; gap: 12px;
  }
  .brand-square {
    width: 26px; height: 26px; background: var(--accent-red);
  }
  .brand-name {
    font-weight: 700; font-size: 26px; letter-spacing: 2px;
    text-transform: uppercase; color: var(--ink);
  }

  .back-brand {
    position: absolute; left: 30px; top: 0; bottom: 0; width: 190px;
    display: flex; flex-direction: column; align-items: center; justify-content: center; gap: 12px;
  }
  .back-brand .brand-square { width: 34px; height: 34px; background: var(--ink-soft); }
  .back-brand .brand-name { font-size: 17px; letter-spacing: 1.5px; color: var(--ink-soft); text-align: center; line-height: 1.3; }

  .back-rule {
    position: absolute; left: 240px; top: 40px; bottom: 40px;
    width: 1px; background: var(--rule);
  }
  .contact {
    position: absolute; left: 262px; top: 42px; right: 20px;
  }
  .contact-name { font-size: 24px; font-weight: 400; color: var(--ink); }
  .contact-role { font-size: 13px; color: var(--ink-soft); margin: 2px 0 14px; }
  .contact-address { font-size: 12.5px; line-height: 1.5; color: var(--ink-soft); margin-bottom: 8px; }
  .contact-list { list-style: none; }
  .contact-list li {
    display: flex; align-items: flex-start; gap: 10px;
    font-size: 12.5px; line-height: 1.45; color: var(--ink-soft); margin-bottom: 5px;
  }
  .contact-list svg { flex: 0 0 14px; width: 14px; height: 14px; margin-top: 2px; }
</style>
</head>
<body>

<section class="card card-front" aria-label="Card front">
  <div class="front-pattern" role="img" aria-label="Embossed repeating company-name pattern across the card"></div>
  <div class="front-brand">
    <span class="brand-square"></span>
    <span class="brand-name">Veldmark Supplies</span>
  </div>
</section>

<section class="card card-back" aria-label="Card back">
  <div class="back-brand">
    <span class="brand-square"></span>
    <span class="brand-name">Veldmark<br>Supplies</span>
  </div>
  <div class="back-rule"></div>
  <div class="contact">
    <p class="contact-name">Dale Harwick</p>
    <p class="contact-role">Owner</p>
    <p class="contact-address">412 W Larkspur Rd Suite 5,<br>Marlow Flats, TX 79000, United States</p>
    <ul class="contact-list">
      <li>
        <svg viewBox="0 0 16 16" aria-hidden="true"><path d="M3 2h3l1.5 3.5-2 1.2a8 8 0 0 0 3.8 3.8l1.2-2L14 10v3a1 1 0 0 1-1 1A11 11 0 0 1 2 3a1 1 0 0 1 1-1z" fill="#c9c9c9"/></svg>
        (555)214-0387
      </li>
      <li>
        <svg viewBox="0 0 16 16" aria-hidden="true"><rect x="1.5" y="3.5" width="13" height="9" fill="none" stroke="#c9c9c9" stroke-width="1.4"/><path d="M1.5 3.5 8 9l6.5-5.5" fill="none" stroke="#c9c9c9" stroke-width="1.4"/></svg>
        sales@veldmarksupplies.com
      </li>
      <li>
        <svg viewBox="0 0 16 16" aria-hidden="true"><circle cx="8" cy="8" r="6.3" fill="none" stroke="#c9c9c9" stroke-width="1.4"/><ellipse cx="8" cy="8" rx="2.8" ry="6.3" fill="none" stroke="#c9c9c9" stroke-width="1.1"/><path d="M1.7 8h12.6" stroke="#c9c9c9" stroke-width="1.1"/></svg>
        www.veldmarksupplies.com
      </li>
      <li>
        <svg viewBox="0 0 16 16" aria-hidden="true"><circle cx="8" cy="9" r="5.5" fill="none" stroke="#c9c9c9" stroke-width="1.4"/><path d="M8 6v3.2l2 1.3" fill="none" stroke="#c9c9c9" stroke-width="1.3"/><path d="M2 3.5 4 1.8M14 3.5 12 1.8" stroke="#c9c9c9" stroke-width="1.3"/></svg>
        Monday – Friday<br>8:30am – 5pm
      </li>
    </ul>
  </div>
</section>

</body>
</html>
```